Social Media Graphics - Oakline Push REVISED

Create 6-7 individual social media graphics (square size) to encourage folks to join our online course called:

The Harvest Ledger Circle
How to Launch a Multi-Million Business From Scratch
Sign Up Today!

IMPORTANT: Make the largest and most prominent text on the graphic be: How to Launch a Multi-Million Business From Scratch

For the color scheme of the graphics, let's try a blue color palette; make sure the graphics appeal to both men and women

Make sure each graphic contains 1 of the 3 pics attached (crop pic as needed); and make sure one of the graphics is all TEXT only.

Target Market(s)

men and women looking to start a business

Industry/Entity Type

Entrepreneurship

Colors
0054AA
0677BA
7BADD7
CADEEF
E8F1F8

Requirements
Must have
• All the text and use the 3 pics provided; one graphic can be all text; Simple, modern design that's easy to read

```html
<!DOCTYPE html>
<html lang="en">
<head>
<meta charset="utf-8">
<title>The Harvest Ledger Circle – Social Graphics</title>
<link href="https://fonts.googleapis.com/css2?family=Archivo+Black&family=Montserrat:wght@800;900&display=swap" rel="stylesheet">
<style>
  :root {
    --canvas-bg: #1c2033;
    --blue-deep: #0a3c86;
    --blue-mid: #0b62ae;
    --blue-bright: #2aa0da;
    --photo-light: #7badd7;
    --photo-pale: #cadeef;
    --pill-dark: #161b2e;
    --white: #ffffff;
  }
  * { margin: 0; padding: 0; box-sizing: border-box; }
  html, body {
    width: 1200px; height: 409px; overflow: hidden;
    background: var(--canvas-bg);
  }
  .canvas { position: relative; width: 1200px; height: 409px; }

  .graphic {
    position: absolute;
    width: 372px;
    height: 328px;
    overflow: hidden;
    background:
      radial-gradient(ellipse 70% 55% at 50% 28%, var(--blue-bright) 0%, var(--blue-mid) 55%, var(--blue-deep) 100%);
    color: var(--white);
    text-align: center;
  }
  .graphic--one { left: 25px; top: 21px; }
  .graphic--two { left: 415px; top: 17px; }
  .graphic--three { left: 804px; top: 18px; }

  .course-kicker {
    position: absolute; left: 0; right: 0; top: 10px;
    font-family: "Archivo Black", sans-serif;
    font-size: 21px; line-height: 22px; letter-spacing: 0.3px;
  }
  .course-name {
    position: absolute; left: 0; right: 0; top: 32px;
    font-family: "Archivo Black", sans-serif;
    font-size: 37px; line-height: 40px; letter-spacing: -0.5px;
  }

  .photo {
    position: absolute;
    top: 74px; height: 155px;
    left: 82px; width: 214px;
    background: linear-gradient(180deg, rgba(20,24,40,0.55) 0%, rgba(20,24,40,0.85) 100%);
    border-radius: 60px 60px 0 0;
  }
  .graphic--two .photo {
    left: 23px; width: 345px; top: 69px; height: 160px;
    border-radius: 0;
    background:
      linear-gradient(180deg, rgba(11,98,174,0) 70%, var(--blue-mid) 100%),
      radial-gradient(ellipse 60% 70% at 55% 45%, var(--photo-pale) 0%, var(--photo-light) 55%, #3a6fa8 100%);
  }
  .graphic--three .photo {
    background:
      linear-gradient(90deg, rgba(214,58,90,0.8) 0%, rgba(214,58,90,0.8) 48%, rgba(30,32,40,0.85) 52%, rgba(30,32,40,0.85) 100%);
  }

  .headline-pill {
    position: absolute; left: 44px; width: 284px; top: 229px; height: 36px;
    background: var(--pill-dark);
    border: 2px solid var(--white);
    border-bottom-color: transparent;
    border-radius: 20px;
    font-family: "Montserrat", sans-serif; font-weight: 900;
    font-size: 26px; line-height: 33px; letter-spacing: -0.2px;
    box-shadow: 0 2px 4px rgba(0,0,0,0.35);
  }
  .headline-sub {
    position: absolute; left: 0; right: 0; top: 266px;
    font-family: "Montserrat", sans-serif; font-weight: 900;
    font-size: 21px; line-height: 26px; letter-spacing: 0.2px;
  }
  .headline-main {
    position: absolute; left: 0; right: 0; top: 291px;
    font-family: "Montserrat", sans-serif; font-weight: 900;
    font-size: 24px; line-height: 28px; letter-spacing: 0.4px;
  }

  .cta {
    position: absolute; width: 372px; text-align: center;
    font-family: "Montserrat", sans-serif; font-weight: 800;
    font-size: 18px; line-height: 20px; color: var(--white);
  }
  .cta--one { left: 25px; top: 353px; }
  .cta--two { left: 415px; top: 348px; }
  .cta--three { left: 804px; top: 349px; }

  .footer-band {
    position: absolute; width: 372px; height: 18px;
    background: linear-gradient(180deg, #0a3f8c, #083276);
  }
  .footer-band--one { left: 25px; top: 375px; }
  .footer-band--two { left: 415px; top: 370px; }
  .footer-band--three { left: 804px; top: 371px; }
</style>
</head>
<body>
<div class="canvas">

  <section class="graphic graphic--one">
    <div class="course-kicker">THE HARVEST</div>
    <div class="course-name">LEDGER CIRCLE</div>
    <div class="photo" role="img" aria-label="Portrait of the two course hosts standing together, smiling"></div>
    <div class="headline-pill">HOW TO LAUNCH A</div>
    <div class="headline-sub">MULTI-MILLION&nbsp; BUSINESS</div>
    <div class="headline-main">FROM SCRATCH</div>
  </section>
  <div class="cta cta--one">SIGN UP TODAY!</div>
  <div class="footer-band footer-band--one"></div>

  <section class="graphic graphic--two">
    <div class="course-kicker">THE HARVEST</div>
    <div class="course-name">LEDGER CIRCLE</div>
    <div class="photo" role="img" aria-label="The two course hosts speaking on stage in a bright room"></div>
    <div class="headline-pill">HOW TO LAUNCH A</div>
    <div class="headline-sub">MULTI-MILLION&nbsp; BUSINESS</div>
    <div class="headline-main">FROM SCRATCH</div>
  </section>
  <div class="cta cta--two">SIGN UP TODAY!</div>
  <div class="footer-band footer-band--two"></div>

  <section class="graphic graphic--three">
    <div class="course-kicker">THE HARVEST</div>
    <div class="course-name">LEDGER CIRCLE</div>
    <div class="photo" role="img" aria-label="The two course hosts posing side by side with arms crossed"></div>
    <div class="headline-pill">HOW TO LAUNCH A</div>
    <div class="headline-sub">MULTI-MILLION&nbsp; BUSINESS</div>
    <div class="headline-main">FROM SCRATCH</div>
  </section>
  <div class="cta cta--three">SIGN UP TODAY!</div>
  <div class="footer-band footer-band--three"></div>

</div>
</body>
</html>
```